Brightmill Data Works

Our company is about IT hardwares and IT solutions. IT hardware such as PC, RAMS, storage and servers. IT solutions such as project management, BA. We are also selling new technology too.

Target Market(s)

Consumer, Small to Medium Business, Corporate

Requirements
Must have
• The business card must have the following:
• Name:
• Title:
• Contact Number:
• Email address:
• Website:
• Color: Must match the logo color upgrade

```html
<!DOCTYPE html>
<html lang="en">
<head>
<meta charset="utf-8">
<title>Brightmill Data Works — Business Card</title>
<link href="https://fonts.googleapis.com/css2?family=Saira:wght@700&family=Arimo:wght@400;700&display=swap" rel="stylesheet">
<style>
  :root {
    --page-bg: #2b2b2c;
    --card-orange: #e29d3c;
    --card-orange-deep: #d08a2a;
    --card-dark: #262627;
    --ink-light: #ececec;
    --ink-mid: #d9d9d9;
    --accent: #e09a34;
    --mark-grey: #4a4a4a;
  }
  * { box-sizing: border-box; margin: 0; padding: 0; }
  html, body {
    width: 1200px;
    height: 997px;
    overflow: hidden;
    background: var(--page-bg);
  }
  .canvas {
    position: relative;
    width: 1200px;
    height: 997px;
  }
  .card {
    position: absolute;
    width: 540px;
    height: 310px;
    border-radius: 20px;
    box-shadow: 0 14px 30px rgba(0,0,0,0.45);
    overflow: hidden;
  }

  /* Front of card */
  .card-front {
    left: 90px;
    top: 150px;
    background: linear-gradient(135deg, var(--card-orange) 0%, var(--card-orange-deep) 100%);
    display: flex;
    align-items: center;
    justify-content: center;
    gap: 18px;
  }
  .front-dot {
    width: 30px;
    height: 30px;
    border-radius: 50%;
    background: var(--mark-grey);
  }
  .front-name {
    font-family: "Saira", sans-serif;
    font-weight: 700;
    font-size: 36px;
    letter-spacing: 0.5px;
    text-transform: uppercase;
    color: var(--ink-light);
  }

  /* Back of card */
  .card-back {
    left: 570px;
    top: 470px;
    background: var(--card-dark);
    padding: 48px 34px 30px 40px;
  }
  .back-name {
    font-family: "Saira", sans-serif;
    font-weight: 700;
    font-size: 30px;
    text-transform: uppercase;
    color: var(--ink-light);
    text-align: center;
    letter-spacing: 0.5px;
  }
  .rule-top {
    position: absolute;
    left: 40px;
    right: 34px;
    top: 118px;
    height: 1px;
    background: var(--accent);
  }
  .person {
    position: absolute;
    left: 40px;
    top: 150px;
    right: 34px;
    display: flex;
    align-items: flex-start;
  }
  .person-block { flex: none; }
  .person-name {
    font-family: "Arimo", sans-serif;
    font-weight: 700;
    font-size: 17px;
    text-transform: uppercase;
    color: var(--accent);
  }
  .person-title {
    font-family: "Arimo", sans-serif;
    font-size: 15px;
    color: var(--ink-mid);
    margin-top: 3px;
  }
  .rule-name {
    flex: 1;
    height: 1px;
    background: var(--accent);
    margin: 11px 0 0 12px;
  }
  .contacts {
    position: absolute;
    left: 40px;
    bottom: 28px;
    list-style: none;
    font-family: "Arimo", sans-serif;
    font-size: 15px;
    color: var(--ink-mid);
  }
  .contacts li {
    display: flex;
    align-items: center;
    gap: 10px;
    margin-top: 6px;
  }
  .contact-icon { width: 14px; height: 14px; flex: none; }
  .website {
    position: absolute;
    right: 34px;
    bottom: 104px;
    font-family: "Arimo", sans-serif;
    font-size: 14px;
    letter-spacing: 1px;
    color: var(--accent);
  }
</style>
</head>
<body>
<main class="canvas">

  <section class="card card-front" aria-label="Business card front">
    <span class="front-dot"></span>
    <span class="front-name">Brightmill Data Works</span>
  </section>

  <section class="card card-back" aria-label="Business card back">
    <h1 class="back-name">Brightmill Data Works</h1>
    <div class="rule-top"></div>

    <div class="person">
      <div class="person-block">
        <p class="person-name">Dana Corwell</p>
        <p class="person-title">Director</p>
      </div>
      <div class="rule-name"></div>
    </div>

    <p class="website">www.brightmilldw.com</p>

    <ul class="contacts">
      <li>
        <svg class="contact-icon" viewBox="0 0 14 14" aria-hidden="true">
          <circle cx="7" cy="7" r="7" fill="#e09a34"/>
          <path d="M4 4.2c0 3.2 2.6 5.8 5.8 5.8l.8-1.2-1.6-.9-.7.7C7.2 8.1 5.9 6.8 5.4 5.7l.7-.7-.9-1.6z" fill="#262627"/>
        </svg>
        555.014.2861
      </li>
      <li>
        <svg class="contact-icon" viewBox="0 0 14 14" aria-hidden="true">
          <circle cx="7" cy="7" r="7" fill="#e09a34"/>
          <path d="M4 4.2c0 3.2 2.6 5.8 5.8 5.8l.8-1.2-1.6-.9-.7.7C7.2 8.1 5.9 6.8 5.4 5.7l.7-.7-.9-1.6z" fill="#262627"/>
        </svg>
        555.017.3390
      </li>
      <li>
        <svg class="contact-icon" viewBox="0 0 14 14" aria-hidden="true">
          <circle cx="7" cy="7" r="7" fill="#e09a34"/>
          <rect x="3.6" y="4.8" width="6.8" height="4.6" fill="none" stroke="#262627" stroke-width="1"/>
          <path d="M3.6 4.8 7 7.5l3.4-2.7" fill="none" stroke="#262627" stroke-width="1"/>
        </svg>
        dana@brightmilldw.com
      </li>
    </ul>
  </section>

</main>
</body>
</html>
```